Automotive Accessories Business Card

Design a business template that match our new logo design and our industry.

https://www.qelmotorgear.com/

Target Market(s)

Aftermarket auto parts and accessories

Industry/Entity Type

automotive

Contact Information for Business Card

company logo

Font styles to use
Serif
Sans Serif

Colors
EB3D1F
EC4F4E
F09395
F8D3D4
FCEDEE

```html
<!DOCTYPE html>
<html lang="en">
<head>
<meta charset="utf-8">
<title>QEL Motor Gear – Business Card</title>
<link href="https://fonts.googleapis.com/css2?family=Montserrat:wght@400;500;700;800&display=swap" rel="stylesheet">
<style>
  :root {
    --backdrop: #e8e8e8;
    --card-dark: #434343;
    --card-panel: #4b4b4b;
    --brand-red: #e0252b;
    --text-white: #ffffff;
    --text-soft: #e4e4e4;
  }
  * { box-sizing: border-box; margin: 0; padding: 0; }
  html, body { width: 1200px; height: 802px; overflow: hidden; }
  body {
    background: var(--backdrop);
    font-family: "Montserrat", sans-serif;
    position: relative;
  }
  .card {
    position: absolute;
    width: 530px;
    height: 303px;
    background: var(--card-dark);
    border-left: 3px solid var(--brand-red);
    border-bottom: 3px solid var(--brand-red);
    box-shadow: 0 10px 24px rgba(0,0,0,0.22);
    overflow: hidden;
  }
  .card--front { left: 50px; top: 110px; }
  .card--back { left: 620px; top: 390px; }

  /* front */
  .front-panel {
    position: absolute; right: 0; top: 0;
    width: 190px; height: 100%;
    background: var(--card-panel);
  }
  .front-strip {
    position: absolute; left: 0; bottom: 0;
    width: 100%; height: 12px; display: flex;
  }
  .front-strip .strip-red { flex: 1; background: var(--brand-red); }
  .front-strip .strip-white { flex: 1; background: var(--text-white); }

  .brand {
    display: flex; align-items: center; gap: 10px;
    color: var(--text-white); font-weight: 800;
    letter-spacing: 0.5px; white-space: nowrap;
  }
  .brand__mark { width: 14px; height: 14px; background: var(--brand-red); flex: none; }
  .card--front .brand { position: absolute; left: 36px; top: 62px; font-size: 26px; }

  .address {
    position: absolute; right: 24px; top: 30px;
    text-align: right; color: var(--text-soft);
    font-size: 12px; line-height: 1.55;
  }
  .person { position: absolute; left: 36px; top: 150px; }
  .person__name {
    color: var(--brand-red); font-weight: 800;
    font-size: 17px; letter-spacing: 2px; text-transform: uppercase;
  }
  .person__role { color: var(--text-soft); font-size: 12px; margin-top: 2px; }
  .contacts { position: absolute; left: 36px; top: 210px; list-style: none; }
  .contacts li {
    display: flex; align-items: center; gap: 8px;
    color: var(--text-soft); font-size: 12px; line-height: 1.6;
  }
  .contacts svg { width: 10px; height: 10px; fill: var(--brand-red); flex: none; }

  /* back */
  .card--back .brand {
    position: absolute; left: 0; right: 0; top: 0; bottom: 0;
    justify-content: center; font-size: 34px;
  }
</style>
</head>
<body>

<section class="card card--front" aria-label="Business card front">
  <div class="front-panel"></div>
  <div class="front-strip"><span class="strip-red"></span><span class="strip-white"></span></div>

  <div class="brand"><span class="brand__mark"></span>QEL MOTOR GEAR INC</div>

  <address class="address">
    240 W. Harbor Ave.<br>Unit B<br>Riverside, CA 92501
  </address>

  <div class="person">
    <p class="person__name">Daniel Reyes</p>
    <p class="person__role">Manager</p>
  </div>

  <ul class="contacts">
    <li>
      <svg viewBox="0 0 10 10"><path d="M2 0.5 L3.6 2.6 L2.8 3.6 Q4 6 6.4 7.2 L7.4 6.4 L9.5 8 L8.4 9.5 Q3 8.5 0.5 1.6 Z"/></svg>
      1-866-555-0142
    </li>
    <li>
      <svg viewBox="0 0 10 10"><path d="M0 2 H10 V8 H0 Z M0.8 2.6 L5 5.6 L9.2 2.6 V3.4 L5 6.4 L0.8 3.4 Z" fill-rule="evenodd"/></svg>
      sales@qelmotorgear.com
    </li>
    <li>
      <svg viewBox="0 0 10 10"><circle cx="5" cy="5" r="4.5"/></svg>
      www.qelmotorgear.com
    </li>
  </ul>
</section>

<section class="card card--back" aria-label="Business card back">
  <div class="brand"><span class="brand__mark"></span>QEL MOTOR GEAR INC</div>
</section>

</body>
</html>
```